Environmental Consultancey needs Web Design

A consultancey firm based in Papua New Guinea specialising servicing a client market primarily in Melanesia, the wider Pacific Region and South East Asia. The firm provides services to community development and resource extraction activites that incorporate sustainable livelihoods for local customary land owners with environmentally responsibile practices and a focus on maintaining biodiversity and ecosystem services. We aim to encompass Culture, Custom and Science in our approach. Our website preferentially will convey a relaxed Pacific Island feel in its colours and design rather than a sterile corporate feel. See attached logo that will need to be visible on page or which may provide basis for ideas for the page.

Target Market(s)

Our target market is primarily the oil, gas and mining industry, secondarily international donor and aid programs followed by government projects and not for profit programs. Services include:
1. Biodiversity and Conservation - Fauna and Flora survey, assessment, management, monitoring & research, protected areas & endangered & threatend species.
2. Social & Community - impact, stakeholder engagement, census and survey, land and community affairs, capacity building empowerment.
3. Environmental Management - sustainable use, enterprise development & management, biodiversity offsets.

Industry/Entity Type

Community

Requirements
Must have
• Multiple pages, Logo somewhere on home page. Space for a couple of photos that as yet ive not decieded upon.
Nice to have
• Perhaps incorporate shapes, texture and colours that convey a feel of the attached photo of a blue bird of paradise. The blue fine overlapping and interlocking feather patterns are appealing perhaps as a background and the other colours used in boarders ? Abstract is fine as would be symbolic images or tribal ambience. The company is all about blending humanity in all its forms with the environment.

```html
<!DOCTYPE html>
<html lang="en">
<head>
<meta charset="utf-8">
<title>Reefline Habitats</title>
<link rel="stylesheet" href="https://fonts.googleapis.com/css2?family=Cinzel:wght@600&family=Open+Sans:wght@300;400&family=PT+Sans:wght@400;700&display=swap">
<style>
:root{
  --leaf:#8fb51f;
  --leaf-light:#c7df3c;
  --leaf-deep:#6f9a12;
  --leaf-text:#6c9a16;
  --ink:#2c2c2c;
  --body:#3a3a3a;
  --link:#2aa3b8;
  --charcoal:#2b2c27;
  --paper:#f4f4f4;
}
*{margin:0;padding:0;box-sizing:border-box}
html,body{width:1145px;height:1200px;overflow:hidden}
body{position:relative;background:var(--paper);font-family:"PT Sans",Arial,sans-serif;color:var(--body)}
.abs{position:absolute}

/* header */
.header{left:0;top:0;width:1145px;height:161px;background:linear-gradient(#ffffff,#f1f1f1)}
.brand{left:44px;top:40px;display:flex;align-items:center;gap:10px;font-family:"PT Sans",Arial,sans-serif;font-size:19px;font-weight:700;color:var(--leaf-deep)}
.brand-dot{width:26px;height:26px;border-radius:50%;background:var(--leaf-deep)}
.social{left:608px;top:22px;display:flex;gap:10px}
.social span{width:44px;height:40px;border-radius:6px;background:linear-gradient(#a6cf3a,#6f9e1a)}
.search{left:894px;top:33px;width:205px;height:26px;border:1px solid #c9c9c9;border-radius:3px;background:#fff;box-shadow:inset 0 1px 3px rgba(0,0,0,.12);font-size:12px;font-style:italic;color:#a0a0a0;padding:5px 14px}
.search svg{position:absolute;right:6px;top:6px}
.nav{left:461px;top:89px;height:49px;display:flex;border-radius:5px;overflow:hidden;background:linear-gradient(#d4eb5a,#a8cd2a 55%,#8eb81c);box-shadow:0 3px 5px rgba(0,0,0,.18)}
.nav a{display:flex;align-items:center;justify-content:center;font-family:"Open Sans",Arial,sans-serif;font-size:14.5px;color:#2f3a10;text-decoration:none;border-right:1px solid rgba(90,120,10,.35);height:100%}
.nav a:last-child{border-right:0}
.nav a.current{background:linear-gradient(#a9cf2c,#8fb51f)}

/* hero */
.hero{left:0;top:161px;width:1145px;height:349px;background:radial-gradient(ellipse at 55% 30%,#c8e04a 0%,#a2c62b 45%,#77a014 100%);overflow:hidden}
.hero-art{left:60px;top:120px;width:430px;height:390px;border-radius:40% 40% 0 0;background:radial-gradient(circle at 70% 68%,#4aa7e0 0 22%,transparent 23%),linear-gradient(160deg,#4f7fc6 0%,#b96a3a 35%,#8a7350 60%,rgba(160,200,60,.2) 100%)}
.hero-title{left:515px;top:218px;font-family:"Cinzel",Georgia,serif;font-weight:600;font-size:41px;line-height:49px;color:#fff;letter-spacing:1px}
.hero-text{left:520px;top:338px;width:488px;font-size:13px;line-height:19.5px;color:#fff;text-align:justify}
.hero-btn{left:922px;top:434px;width:81px;height:26px;border-radius:5px;background:linear-gradient(#ffffff,#d3d3d3);box-shadow:0 2px 3px rgba(0,0,0,.3);font-size:12px;font-weight:700;color:#3b3b3b;display:flex;align-items:center;justify-content:center}

/* welcome */
.welcome-title{left:41px;top:537px;font-family:"Open Sans",Arial,sans-serif;font-weight:400;font-size:24px;color:var(--leaf-text)}
.welcome-text{left:41px;top:581px;width:683px;font-size:13.5px;line-height:22px;text-align:justify}
.video{left:749px;top:540px;width:336px;height:188px;background:#111;padding:4px;box-shadow:0 14px 16px -10px rgba(0,0,0,.45)}
.video-shot{width:328px;height:168px;background:radial-gradient(circle at 48% 40%,#6f7e5a 0,#98a5a0 35%,#7d8a80 70%,#4b5a3a 100%)}
.video-play{left:147px;top:62px}
.video-bar{left:4px;top:172px;width:328px;height:12px;background:#1b1b1b}
.video-bar i{position:absolute;left:30px;top:5px;width:250px;height:3px;background:#555}

/* cards */
.card{top:761px;width:350px;height:235px;border-radius:34px 34px 0 0;background:linear-gradient(#e9e9e9,#f6f6f6 40%,rgba(246,246,246,0));padding:0 18px}
.card h3{font-family:"Open Sans",Arial,sans-serif;font-weight:400;font-size:18.5px;color:var(--leaf-text);position:absolute;top:22px;left:103px}
.card .icon{position:absolute;left:52px;top:18px;width:38px;height:38px}
.card p{position:absolute;font-size:13.3px;line-height:22px;text-align:justify}
.entry{position:absolute;left:35px;width:300px;font-size:13.3px;line-height:21px}
.entry b{display:block;font-weight:700;color:var(--ink)}
.entry::before{content:"";position:absolute;left:-18px;top:6px;border-left:6px solid #555;border-top:4px solid transparent;border-bottom:4px solid transparent}
.entry a{color:var(--link);text-decoration:none}
.more{position:absolute;right:22px;top:177px;font-size:13px}

/* footer */
.footer{left:0;top:996px;width:1145px;height:144px;background:linear-gradient(#9cc32a,#8db61e);border-top:2px solid #7da516}
.footer h4{position:absolute;font-family:"Open Sans",Arial,sans-serif;font-weight:400;font-size:13.5px;color:#1f2a06;top:21px}
.mail{position:absolute;left:44px;top:52px;width:206px;height:26px;background:#fff;border:1px solid #b7b7b7;border-radius:2px;font-size:12px;font-style:italic;color:#a0a0a0;padding:5px 16px}
.submit{position:absolute;left:186px;top:89px;width:63px;height:25px;background:linear-gradient(#5d5d5d,#363636);color:#fff;font-size:13px;display:flex;align-items:center;justify-content:center}
.divider{position:absolute;top:24px;width:2px;height:100px;background:#6b8f14}
.links{position:absolute;left:311px;top:51px;display:grid;grid-template-columns:175px 176px 160px;row-gap:6px}
.links a{font-size:12px;color:#2a3208;text-decoration:underline;line-height:18px}
.arrows{position:absolute;left:1071px;top:22px;display:flex;gap:8px}
.partners{position:absolute;left:843px;top:56px;width:255px;height:58px;background:linear-gradient(#ffffff,#e1e1e1);display:flex;align-items:center;justify-content:space-around;padding:0 18px;box-shadow:0 2px 3px rgba(0,0,0,.2)}
.partners span{width:90px;height:20px;background:#9b9b9b;border-radius:3px}
.bottom{left:0;top:1140px;width:1145px;height:60px;background:linear-gradient(#3a3b34,var(--charcoal));color:#e6e6e6;font-size:12px;display:flex;align-items:center;justify-content:center}
</style>
</head>
<body>
<header class="abs header">
  <div class="abs brand"><span class="brand-dot"></span>Reefline Habitats</div>
  <div class="abs social" aria-label="Social links"><span></span><span></span><span></span><span></span><span></span></div>
  <div class="abs search">Search
    <svg width="12" height="12" viewBox="0 0 12 12"><circle cx="5" cy="5" r="3.6" fill="none" stroke="#aaa" stroke-width="1.4"/><path d="M7.6 7.6L11 11" stroke="#aaa" stroke-width="1.6"/></svg>
  </div>
  <nav class="abs nav">
    <a class="current" style="width:110px">Home</a>
    <a style="width:104px">About us</a>
    <a style="width:99px">Services</a>
    <a style="width:122px">Latest News</a>
    <a style="width:71px">Links</a>
    <a style="width:133px">Contact us</a>
  </nav>
</header>

<section class="abs hero">
  <h1 class="abs hero-title" style="top:57px">Encompassing Culture,<br>Custom &amp; Science</h1>
  <p class="abs hero-text" style="top:177px">Neque porro quisquam est, qui dolorem ipsum quia dolor sit amet, consectetur, adipisci velit, sed quia non numquam eius modi tempora incidunt ut labore et dolore magnam aliquam quaerat voluptatem. Ut enim ad minima veniam, quis nostrum exercitationem ullam.</p>
  <div class="abs hero-btn" style="top:273px">Click Here</div>
</section>
<div class="abs hero-art" role="img" aria-label="Illustration of a bluebird perched on a weathered post beside a glossy globe"></div>

<h2 class="abs welcome-title">Welcome to our site</h2>
<p class="abs welcome-text">Sed ut perspiciatis unde omnis iste natus error sit voluptatem accusantium doloremque laudantium, totam rem aperiam, eaque ipsa quae ab illo inventore veritatis et quasi architecto beatae vitae dicta sunt explicabo. Nemo enim ipsam voluptatem quia voluptas sit aspernatur aut odit aut fugit, sed quia consequuntur magni dolores eos qui ratione voluptatem sequi nesciunt. Neque porro quisquam est, qui dolorem ipsum quia dolor sit amet, consectetur, adipisci velit. Quis autem vel eum iure reprehenderit qui in ea voluptate velit esse quam nihil molestiae consequatur, vel illum qui dolorem eum fugiat quo voluptas nulla pariatur.</p>

<div class="abs video">
  <div class="video-shot" role="img" aria-label="Video still of a hand holding a magnifying glass over a tree"></div>
  <svg class="abs video-play" width="46" height="46" viewBox="0 0 46 46"><circle cx="23" cy="23" r="21" fill="#d9d9d9" stroke="#555" stroke-width="2"/><path d="M18 13L33 23L18 33Z" fill="#333"/></svg>
  <div class="abs video-bar"><svg class="abs" style="left:10px;top:3px" width="8" height="7"><rect width="2.5" height="7" fill="#ddd"/><rect x="5" width="2.5" height="7" fill="#ddd"/></svg><i></i></div>
</div>

<section class="abs card" style="left:39px">
  <span class="icon" style="border-radius:50%;background:var(--leaf-deep);width:32px;height:32px;top:22px"></span>
  <h3>What we do?</h3>
  <p style="left:19px;top:64px;width:315px">Sed ut perspiciatis unde omnis iste natus error sit voluptatem accusantium doloremque laudantium, totam rem aperiam, eaque ipsa quae ab illo inventore veritatis et quasi architecto beatae vitae dicta sunt explicabo. Nemo enim ipsam voluptatem quia voluptas sit aspernatur aut odit aut fugit.</p>
</section>

<section class="abs card" style="left:396px">
  <span class="icon" style="background:#e2621b;border-radius:6px;left:45px;top:18px;width:36px;height:36px"></span>
  <h3 style="left:92px">Blog Archieves</h3>
  <div class="entry" style="top:67px"><b>Totam rem aperiam</b>Eaque ipsa quae ab illo inventore veritatis et quasi architecto beatae vitae dicta sunt explicabo. Nemo enim ipsam voluptatem quia voluptas sit aspernatur aut odit aut fugit.</div>
  <span class="more">View more</span>
</section>

<section class="abs card" style="left:753px">
  <span class="icon" style="border-radius:50%;background:#3e9fd8;left:36px;top:16px;width:34px;height:34px"></span>
  <h3 style="left:84px">Chirp Feeds</h3>
  <div class="entry" style="left:43px;top:67px"><b>Eaque ipsa quaeab</b>Enventore veritatis et quasi architecto beatae vitae<br><a>http://kundaleaf.org/pg56sds/reef8146/sd</a></div>
  <div class="entry" style="left:43px;top:147px"><b>Eaque ipsa quaeab</b><a>http://kundaleaf.org/pg56sds/reef8146/sd</a></div>
</section>

<footer class="abs footer">
  <h4 style="left:45px">News Letter</h4>
  <div class="mail">Enter mial ID</div>
  <div class="submit">SUBMIT</div>
  <span class="divider" style="left:280px"></span>
  <h4 style="left:310px">Our Services</h4>
  <div class="links">
    <a>Modi tempora adipisci</a><a>Modi tempora adipisci</a><a>Modi tempora adipisci</a>
    <a>Dicta sunt explicabo</a><a>Dicta sunt explicabo</a><a>Dicta sunt explicabo</a>
    <a>Quasi architecto</a><a>Quasi architecto</a><a>Quasi architecto</a>
  </div>
  <span class="divider" style="left:815px"></span>
  <h4 style="left:843px">Our Partners</h4>
  <div class="arrows">
    <svg width="8" height="11"><path d="M7 1L2 5.5L7 10" fill="none" stroke="#222" stroke-width="2"/></svg>
    <svg width="8" height="11"><path d="M1 1L6 5.5L1 10" fill="none" stroke="#222" stroke-width="2"/></svg>
  </div>
  <div class="partners"><span></span><span></span></div>
</footer>
<div class="abs bottom">Copyright © 2012 www.reeflinehabitats.com &nbsp;&nbsp; All rights reserved</div>
</body>
</html>
```